BOLD & MINIMALIST DESIGN NEEDED

We want a very bold but minimalistic business card design that is impactful and utilizes both sides of the business card. Our current logo is included for your use.

We want bold fonts and good use of negative space. We don't want the logo to overpower the design.

Target Market(s)

Professionals who are building new commercial buildings.

Industry/Entity Type

Construction

Contact Information for Business Card

Name, Title, email, office phone, cell phone, website

Font styles to use
Serif
Sans Serif

Requirements
Must have
• Bold design!

```html
<!DOCTYPE html>
<html lang="en">
<head>
<meta charset="utf-8">
<title>Northridge Build – Business Card</title>
<link href="https://fonts.googleapis.com/css2?family=Lato:wght@400;700;900&display=swap" rel="stylesheet">
<style>
  :root {
    --stage: #2b2b2b;
    --green: #6aa51f;
    --green-light: #7fbf2a;
    --green-dark: #2f5410;
    --green-mid: #4d7f18;
    --ink: #111111;
    --paper: #ffffff;
    --text: #1a1a1a;
  }
  * { margin: 0; padding: 0; box-sizing: border-box; }
  html, body { width: 1200px; height: 800px; overflow: hidden; }
  body {
    background: var(--stage);
    font-family: "Lato", Arial, sans-serif;
    position: relative;
  }
  .card {
    position: absolute;
    width: 540px;
    height: 308px;
    border-radius: 14px;
    overflow: hidden;
  }

  /* Front side */
  .card-front {
    left: 40px; top: 246px;
    background: radial-gradient(circle at 30% 35%, var(--green-mid) 0%, #3f6c13 55%, var(--green-dark) 100%);
  }
  .front-mark-area {
    position: absolute;
    right: 0; top: 0;
    width: 250px; height: 100%;
    background: linear-gradient(135deg, #151515 0%, #2a3d12 55%, var(--green-light) 100%);
    opacity: .9;
  }
  .brand {
    display: flex;
    align-items: center;
    gap: 10px;
    font-weight: 900;
    text-transform: uppercase;
    letter-spacing: 1px;
    white-space: nowrap;
  }
  .brand-square { width: 18px; height: 18px; }
  .card-front .brand {
    position: absolute;
    left: 40px; top: 134px;
    color: var(--paper);
    font-size: 30px;
  }
  .card-front .brand-square { background: var(--paper); }

  /* Back side */
  .card-back {
    left: 620px; top: 246px;
    background: var(--paper);
  }
  .card-back .brand {
    position: absolute;
    right: 30px; top: 40px;
    color: var(--ink);
    font-size: 26px;
  }
  .card-back .brand-square { background: var(--green); }
  .divider-top {
    position: absolute;
    right: 24px; top: 106px;
    width: 320px; height: 1px;
    background: var(--green);
  }
  .person {
    position: absolute;
    left: 30px; top: 146px;
  }
  .person-name {
    color: var(--green);
    font-weight: 900;
    font-size: 28px;
    line-height: 1;
  }
  .person-title {
    color: var(--text);
    font-size: 15px;
    margin-top: 4px;
  }
  .divider-name {
    width: 190px; height: 1px;
    background: var(--green);
    margin-top: 10px;
  }
  .contact-list {
    list-style: none;
    margin-top: 10px;
  }
  .contact-list li {
    display: flex;
    align-items: center;
    gap: 8px;
    font-size: 14px;
    color: var(--text);
    line-height: 20px;
  }
  .contact-list svg { width: 12px; height: 12px; fill: var(--green); flex: none; }
  .address {
    position: absolute;
    right: 30px; top: 196px;
    text-align: right;
    font-size: 14px;
    line-height: 19px;
    color: var(--text);
  }
  .bottom-band {
    position: absolute;
    left: 0; bottom: 0;
    width: 100%; height: 40px;
  }
  .web {
    position: absolute;
    right: 30px; bottom: 10px;
    display: flex; align-items: center; gap: 8px;
    color: var(--paper);
    font-size: 14px;
  }
  .web svg { width: 14px; height: 14px; }
</style>
</head>
<body>

<section class="card card-front" aria-label="Card front">
  <div class="front-mark-area" role="img" aria-label="Large brand symbol decoration in black and green"></div>
  <div class="brand"><span class="brand-square"></span>Northridge Build</div>
</section>

<section class="card card-back" aria-label="Card back">
  <div class="brand"><span class="brand-square"></span>Northridge Build</div>
  <div class="divider-top"></div>

  <div class="person">
    <div class="person-name">Daniel Carter</div>
    <div class="person-title">Founder &amp; CEO</div>
    <div class="divider-name"></div>
    <ul class="contact-list">
      <li><svg viewBox="0 0 24 24"><path d="M6.6 10.8a15 15 0 0 0 6.6 6.6l2.2-2.2a1 1 0 0 1 1-.25 11.4 11.4 0 0 0 3.6.57 1 1 0 0 1 1 1V20a1 1 0 0 1-1 1A17 17 0 0 1 3 4a1 1 0 0 1 1-1h3.5a1 1 0 0 1 1 1c0 1.25.2 2.45.57 3.6a1 1 0 0 1-.25 1z"/></svg>021-555-304-118</li>
      <li><svg viewBox="0 0 24 24"><path d="M7 2h10a2 2 0 0 1 2 2v16a2 2 0 0 1-2 2H7a2 2 0 0 1-2-2V4a2 2 0 0 1 2-2zm0 3v13h10V5z"/></svg>044-555-872-610</li>
      <li><svg viewBox="0 0 24 24"><path d="M2 11 22 3l-8 19-3-8z"/></svg>info@ridgemail.com</li>
    </ul>
  </div>

  <div class="address">4410 Harbor Ridge Pkwy 212-B,<br>FL 32501</div>

  <svg class="bottom-band" viewBox="0 0 540 40" preserveAspectRatio="none" aria-hidden="true">
    <path d="M0 34 L250 34 Q262 34 266 24 L270 12 Q274 4 286 4 L540 4 L540 40 L0 40 Z" fill="#6aa51f"/>
  </svg>
  <div class="web">
    <svg viewBox="0 0 24 24" fill="none" stroke="#ffffff" stroke-width="2"><circle cx="12" cy="12" r="10"/><path d="M2 12h20M12 2a15 15 0 0 1 0 20M12 2a15 15 0 0 0 0 20"/></svg>
    www.ridgebuild.com
  </div>
</section>

</body>
</html>
```